Cat-products company needs smart, yet endearing, business card

We need a business card design for a new, but up-and-running, business based in Honolulu, Hawaii. The business is Purrnest Nook Co. Our first product is the most environmentally-friendly cat grass kit ever seen on the planet. Future products, currently in the R&D phase, will include a variety of exciting cat scratchers. We also do consulting work to help apartment-dwellers make their home more cat-friendly and, in the future, plan on doing full, custom installs of structure to create high walkways for cats.

Target Market(s)

Middle-aged, apartment-dwelling, middle-class workers who own 1 or more cats and who dote on them.

Industry/Entity Type

Pet Care

Contact Information for Business Card

A striking, professional, yet warm and friendly design is what we're after.

Font styles to use
Serif
Sans Serif
Other font styles liked:
• Comfortaa

Colors

Designer to choose colors to be used in the design.

Requirements
Must have
• The company logo: (see attachment)
• The company name: Purrnest Nook Co
• The web address: www.purrnestnookco.com
• Email: support@purrnestnookco.com
• Phone: +1 (808) 571 6023
• Update (Fri Jun 30 3017 7:45pm Hawaii Time) I would like, is possible, uploaded picture of the cat grass kit on the back of the card with some text along the lines of: Purrnest Nook Co - Maker Of The Leafiest Feline Sprout Set Yet
Nice to have
• A cat picture, cartoon, real or silhouette that illustrates cats in action and/or relaxing; ie using the apartment space to live, play and relax in and being well-contented.
• Most of the website is done in the font: Comfortaa. It might be nice to continue using this for brand consistency.
Should not have
• Hard-to-read fonts.

```html
<!DOCTYPE html>
<html lang="en">
<head>
<meta charset="utf-8">
<title>Purrnest Nook Co – Business Card</title>
<link rel="stylesheet" href="https://fonts.googleapis.com/css2?family=Open+Sans:wght@400;600;700&display=swap">
<style>
  :root {
    --brown: #563229;
    --yellow: #fdb515;
    --white: #ffffff;
    --stage: #efeae6;
  }
  * { margin: 0; padding: 0; box-sizing: border-box; }
  html, body { width: 1200px; height: 900px; overflow: hidden; }
  body {
    position: relative;
    background: var(--stage);
    font-family: "Open Sans", Arial, sans-serif;
  }
  .card {
    position: absolute;
    width: 587px;
    height: 362px;
    overflow: hidden;
    box-shadow: 0 6px 18px rgba(0,0,0,0.18);
  }
  .card-front { left: 78px; top: 35px; background: var(--white); }
  .card-back { left: 388px; top: 497px; width: 567px; height: 360px; background: var(--brown); }

  .front-bands { position: absolute; inset: 0; }

  .brand-name {
    position: absolute;
    display: flex;
    align-items: center;
    gap: 14px;
    font-weight: 700;
    white-space: nowrap;
  }
  .brand-mark { width: 22px; height: 22px; border-radius: 50%; background: var(--yellow); }
  .card-front .brand-name { left: 0; right: 0; top: 68px; justify-content: center; font-size: 46px; color: var(--brown); }
  .card-back .brand-name { left: 0; right: 0; top: 150px; justify-content: center; font-size: 46px; color: var(--yellow); }

  .contact-list {
    position: absolute;
    right: 294px;
    top: 264px;
    list-style: none;
    text-align: right;
    color: var(--white);
    font-size: 15px;
    line-height: 22px;
  }
  .contact-list li { display: flex; align-items: center; justify-content: flex-end; gap: 6px; }
  .contact-icon { width: 13px; height: 13px; fill: var(--yellow); }

  .person {
    position: absolute;
    left: 317px;
    top: 272px;
    color: var(--white);
  }
  .person-name { font-size: 20px; font-weight: 700; line-height: 26px; }
  .person-title { font-size: 15px; line-height: 20px; }
</style>
</head>
<body>

<section class="card card-front" aria-label="Business card front">
  <svg class="front-bands" width="587" height="362" viewBox="0 0 587 362" aria-hidden="true">
    <polygon points="0,198 405,198 382,224 0,224" fill="var(--yellow)"/>
    <polygon points="0,228 384,228 416,190 587,190 587,362 0,362" fill="var(--brown)"/>
  </svg>

  <div class="brand-name"><span class="brand-mark"></span>Purrnest Nook Co</div>

  <ul class="contact-list">
    <li>+1 (808) 571 6023
      <svg class="contact-icon" viewBox="0 0 16 16"><path d="M3.5 1l2.5 3-1.5 1.8a9 9 0 0 0 5.7 5.7L12 10l3 2.5-1.4 2.4C8 15 1 8 1.1 2.4z"/></svg>
    </li>
    <li>support@purrnestnookco.com
      <svg class="contact-icon" viewBox="0 0 16 16"><path d="M1 3h14v10H1z M1.5 3.5L8 9l6.5-5.5" stroke="var(--brown)" stroke-width="1.2"/></svg>
    </li>
    <li>www.purrnestnookco.com
      <svg class="contact-icon" viewBox="0 0 16 16"><circle cx="8" cy="8" r="7"/><path d="M1 8h14M8 1c-3 3.5-3 10.5 0 14M8 1c3 3.5 3 10.5 0 14" stroke="var(--brown)" stroke-width="1" fill="none"/></svg>
    </li>
  </ul>

  <div class="person">
    <p class="person-name">MALIA KAHALE</p>
    <p class="person-title">Managing Director</p>
  </div>
</section>

<section class="card card-back" aria-label="Business card back">
  <div class="brand-name"><span class="brand-mark"></span>Purrnest Nook Co</div>
</section>

</body>
</html>
```